Tandem Hearth Works Pty Ltd

We need business cards for a company based in Perth, we install, service and maintain fire equipment.
On the front we want a great design with our logo and a small spot for our full company name, general company email address and office number. On the back we need space for our name, title, mobile number and email address on the back.

Target Market(s)

Facility managers and commercial/industrial building owners/occupiers.

Contact Information for Business Card

Font styles to use
Sans Serif

Requirements
Must have
• Please only submit 5 of your best samples.
Darker tones are preferred.
Nice to have
• We want to use, black, red and grey. Keep it modern and clean.
I've attached the company logo and a sample of a boarder we use on our emergency plans.
Should not have
• No preference. Let the designer choose.

```html
<!DOCTYPE html>
<html lang="en">
<head>
<meta charset="utf-8">
<title>Tandem Hearth Works – Business Cards</title>
<link href="https://fonts.googleapis.com/css2?family=Montserrat:wght@600;700&family=Roboto:wght@300;400&display=swap" rel="stylesheet">
<style>
  :root {
    --bg: #d9d4cc;
    --card: #1b1c1e;
    --red: #e3202a;
    --grey: #6a6b6e;
    --white: #f2f2f2;
    --rule: #8a8b8e;
  }
  * { margin: 0; padding: 0; box-sizing: border-box; }
  html, body { width: 1200px; height: 859px; overflow: hidden; }
  body { background: var(--bg); position: relative; font-family: "Roboto", Arial, sans-serif; }

  .card {
    position: absolute;
    top: 289px;
    width: 500px;
    height: 285px;
    background: var(--card);
    box-shadow: 0 6px 14px rgba(0,0,0,0.35);
    overflow: hidden;
  }
  .card--back { left: 60px; }
  .card--front { left: 640px; }

  .brand {
    position: absolute;
    left: 17px;
    top: 30px;
    font-family: "Montserrat", Arial, sans-serif;
    font-weight: 700;
    font-size: 62px;
    line-height: 1;
    letter-spacing: 1px;
  }
  .card--back .brand { color: var(--red); }
  .card--front .brand { color: var(--grey); }

  .rule {
    position: absolute;
    left: 17px;
    right: 20px;
    top: 201px;
    height: 1px;
    background: linear-gradient(to right, rgba(138,139,142,0.2), var(--rule) 50%, rgba(138,139,142,0.2));
  }

  .person { position: absolute; left: 18px; top: 226px; }
  .person__name {
    font-family: "Montserrat", Arial, sans-serif;
    font-weight: 700;
    font-size: 21px;
    color: var(--red);
    letter-spacing: 0.5px;
    line-height: 1;
  }
  .person__title { margin-top: 4px; font-size: 13px; font-weight: 300; color: var(--white); }

  .company-name {
    position: absolute;
    left: 17px;
    top: 236px;
    font-family: "Montserrat", Arial, sans-serif;
    font-weight: 700;
    font-size: 12.5px;
    color: var(--red);
    letter-spacing: 0.6px;
    text-transform: uppercase;
  }

  .contact { position: absolute; right: 18px; top: 229px; text-align: right; color: var(--white); }
  .contact__row { display: flex; justify-content: flex-end; align-items: center; gap: 9px; height: 18px; }
  .contact__phone { font-size: 15px; font-weight: 300; }
  .contact__email { font-size: 13px; font-weight: 300; }
  .contact__row svg { width: 13px; height: 13px; flex: none; }

  .accent-bar { position: absolute; bottom: 0; height: 4px; background: var(--red); }
  .card--back .accent-bar { left: 0; width: 172px; }
  .card--front .accent-bar { right: 0; width: 189px; }
</style>
</head>
<body>

<section class="card card--back" aria-label="Business card, personal side">
  <div class="brand">THW</div>
  <div class="rule"></div>
  <div class="person">
    <div class="person__name">OWEN HARTLEY</div>
    <div class="person__title">Owner/ CEO</div>
  </div>
  <div class="contact">
    <div class="contact__row">
      <span class="contact__phone">128 555 0142</span>
      <svg viewBox="0 0 13 13" aria-hidden="true"><rect x="3.5" y="0.8" width="6" height="11.4" rx="1" fill="none" stroke="#e3202a" stroke-width="1.2"/><circle cx="6.5" cy="10.3" r="0.7" fill="#e3202a"/></svg>
    </div>
    <div class="contact__row">
      <span class="contact__email">owenhartley@hearthworks.au</span>
      <svg viewBox="0 0 13 13" aria-hidden="true"><rect x="0.5" y="3" width="12" height="8" fill="#e3202a"/><path d="M0.5 3 L6.5 7.5 L12.5 3" fill="none" stroke="#1b1c1e" stroke-width="1"/></svg>
    </div>
  </div>
  <div class="accent-bar"></div>
</section>

<section class="card card--front" aria-label="Business card, company side">
  <div class="brand">THW</div>
  <div class="rule"></div>
  <div class="company-name">Tandem Hearth Works Pty Ltd</div>
  <div class="contact">
    <div class="contact__row">
      <span class="contact__phone">128 555 0142</span>
      <svg viewBox="0 0 13 13" aria-hidden="true"><path d="M2.5 1 L5 1 L6 4 L4.5 5.2 C5.3 7 6.2 7.9 7.8 8.6 L9 7 L12 8 L12 10.6 C12 11.4 11.3 12 10.5 12 C5.5 11.6 1.4 7.5 1 2.5 C1 1.7 1.7 1 2.5 1 Z" fill="#e3202a"/></svg>
    </div>
    <div class="contact__row">
      <span class="contact__email">hello@tandemhearth.au</span>
      <svg viewBox="0 0 13 13" aria-hidden="true"><rect x="0.5" y="3" width="12" height="8" fill="#e3202a"/><path d="M0.5 3 L6.5 7.5 L12.5 3" fill="none" stroke="#1b1c1e" stroke-width="1"/></svg>
    </div>
  </div>
  <div class="accent-bar"></div>
</section>

</body>
</html>
```